Social Media App Needs PPT Template

We need a PowerPoint template for a new social media company based in the DC area called "Bold Ledger." We provide an interactive digital platform for executives to share actionable advice. We would like to see designs that use our orange logo color as an accent, but are mainly grey, white, and black. The final design should communicate clean, chic, modern, and professional.

Target Market(s)

Executives

Industry/Entity Type

Information Technology

Font styles to use
Sans Serif

Colors
f78f20
fbe7d2
ffffff
000000
e8e8e8
757575

Requirements
Must have
• My project must have title page and many options for the body of the ppt (graphs, tables, etc). It also needs to be easy to modify. I must have someone who is experienced in creating powerpoint templates.
Nice to have
• It would be nice to have a very modern and clean design that includes the logo on every page, but still leaves a lot of room for the content of the slide
Should not have
• My design project should not look to busy.

```html
<!DOCTYPE html>
<html lang="en">
<head>
<meta charset="utf-8">
<title>Bold Ledger – Transition Page</title>
<link rel="stylesheet" href="https://fonts.googleapis.com/css2?family=Lato:wght@300;400&display=swap">
<style>
  :root {
    --stage-grey: #575757;
    --label-white: #f2f2f2;
    --accent-orange: #f78f20;
    --band-black: #03070c;
    --band-charcoal: #0b1118;
    --photo-warm-grey: #8a8486;
    --photo-slate: #4a5560;
    --photo-steel: #2e3a46;
    --photo-deep: #141b23;
    --title-white: #ffffff;
  }
  * { margin: 0; padding: 0; box-sizing: border-box; }
  html, body {
    width: 1200px;
    height: 960px;
    overflow: hidden;
    background: var(--stage-grey);
    font-family: "Lato", "Helvetica Neue", Arial, sans-serif;
  }
  .canvas {
    position: relative;
    width: 1200px;
    height: 960px;
  }
  .page-label {
    position: absolute;
    top: 76px;
    left: 0;
    width: 1200px;
    text-align: center;
    font-weight: 300;
    font-size: 26px;
    line-height: 32px;
    color: var(--label-white);
    letter-spacing: 0.5px;
  }
  .slide {
    position: absolute;
    left: 123px;
    top: 159px;
    width: 987px;
    height: 740px;
    overflow: hidden;
    background: var(--photo-deep);
  }
  .slide-photo {
    position: absolute;
    inset: 0;
    background: linear-gradient(35deg,
      var(--photo-warm-grey) 0%,
      var(--photo-slate) 30%,
      var(--photo-steel) 60%,
      var(--photo-deep) 100%);
  }
  .title-band {
    position: absolute;
    left: 0;
    top: 585px;
    width: 987px;
    height: 116px;
  }
  .title-band svg { display: block; }
  .slide-title {
    position: absolute;
    left: 519px;
    top: 585px;
    height: 116px;
    line-height: 116px;
    font-weight: 300;
    font-size: 58px;
    color: var(--title-white);
    letter-spacing: 0.5px;
    white-space: nowrap;
  }
</style>
</head>
<body>
  <main class="canvas">
    <p class="page-label">Page 2</p>

    <section class="slide">
      <div class="slide-photo" role="img" aria-label="Photo of two hands in a knit sweater holding a smartphone, with glowing app and social icons floating over a dark background"></div>

      <div class="title-band">
        <svg width="987" height="116" viewBox="0 0 987 116" aria-hidden="true">
          <defs>
            <linearGradient id="band-fill" x1="0" y1="0" x2="1" y2="0">
              <stop offset="0" stop-color="#03070c"/>
              <stop offset="1" stop-color="#0b1118"/>
            </linearGradient>
          </defs>
          <polygon class="band-shape" points="446,0 987,0 987,116 328,116" fill="url(#band-fill)"/>
          <polygon class="accent-stripe" points="401,0 436,0 316,116 281,116" fill="var(--accent-orange)"/>
        </svg>
      </div>

      <h1 class="slide-title">Transition Page</h1>
    </section>
  </main>
</body>
</html>
```